BRAMBLEFORD CONSTRUCTIONS B-Card

I currently have a b-card design but will be removing the image (tree) from the logo and have text only.
I want the card to be classy and strong within the building and construction industry.
I will be using Spot UV on the cards as per the attached examples. I will also send through some sketched ideas that I have in mind.
The color blue is similar to the image (No. 6) attached images

Target Market(s)

middle to maturre aged.
Home Owners / Renovators and Builders

Industry/Entity Type

Construction

Contact Information for Business Card

BRAMBLEFORD CONSTRUCTIONS
Name: Gareth Pennick
Title: Project Manager
Mobile: 0427 351 804
Office: (08) 9316 5172
Address: 47C Corvell Street, Malaga WA 6090
Email: info@bramblefordhomes.com.au
PO Box: 3817 Malaga WA 6944

Colors
0592cd
33a6d7
85cae6
1b1b1b

Requirements
Must have
• 1. It must have spot UV on the front of card, maybe back of card too
• 2. I really like the blue on image 6. (or at least a really cool electric blue against the charcoal grey background)
• 3. The font must be slimline and modern. Easy to read
• 4. There must be no black used on the card... Only greys and dark charcoal greys
• 5. Use only the text from the logo "Brambleford Constructions" Not the image of the tree. I am wanting the b-cards to be more masculine.
Nice to have
• 1. I like the design concept on image 6. but happy to see what else you can do with the Spot UV
• 2. Unless you have a really cool idea of the image of the tree (from previous logo) Spot UV somewhere in the design concept thats original and different then I am keen to see what you come up with
• 3. Try changing the color of the logo eg. full white or Blue and white
• 4. Another option is to have the Brambleford Logo on the front of card with the spot UV in the background of text which we specialise in eg, Roofing, Ceiling, Insulation, Gutter Guards, Electrical, Insurance etc and we can add or reduce items as required. Similar to image 12.
Should not have
• Do not include the image of the tree from previous logo. unless you have a really cool idea of Spot UV somewhere in the design concept thats original and different.

```html
<!DOCTYPE html>
<html lang="en">
<head>
<meta charset="utf-8">
<title>Brambleford Constructions – Business Card</title>
<link rel="stylesheet" href="https://fonts.googleapis.com/css2?family=Jost:wght@400;500;600&display=swap">
<style>
  :root {
    --brand-blue: #1358a2;
    --brand-blue-deep: #0f4c8f;
    --paper-white: #ffffff;
    --stage-grey: #e6e7e9;
    --charcoal: #2e3135;
    --card-w: 620px;
    --card-h: 379px;
  }
  * { box-sizing: border-box; margin: 0; padding: 0; }
  html, body {
    width: 1200px; height: 843px; overflow: hidden;
    background: var(--stage-grey);
    font-family: "Jost", "Futura", sans-serif;
  }
  .stage {
    width: 1200px; height: 843px;
    display: flex; flex-direction: column;
    align-items: center; justify-content: center; gap: 30px;
  }
  .card {
    position: relative;
    width: var(--card-w); height: var(--card-h);
    overflow: hidden;
    box-shadow: 0 6px 18px rgba(40, 44, 52, 0.22);
  }

  /* Front */
  .card--front {
    background: var(--brand-blue);
    color: var(--paper-white);
    display: flex; flex-direction: column;
    align-items: center; justify-content: center;
  }
  .wordmark {
    font-weight: 500;
    text-transform: uppercase;
    text-align: center;
    line-height: 1;
  }
  .wordmark__name { display: block; font-size: 46px; letter-spacing: 0.01em; }
  .wordmark__sub { display: block; font-size: 17px; letter-spacing: 0.62em; margin-top: 6px; padding-left: 0.62em; }
  .card--front .wordmark { color: var(--paper-white); }
  .services {
    margin-top: 26px;
    font-size: 15px; font-weight: 400;
    text-align: center; line-height: 1.35;
    letter-spacing: 0.02em;
  }

  /* Back */
  .card--back { background: var(--brand-blue); }
  .back-panel { position: absolute; inset: 0; }
  .contact {
    position: absolute; left: 42px; top: 44px;
    color: var(--paper-white);
    font-size: 15px; line-height: 1.4;
  }
  .contact__name { font-size: 21px; font-weight: 600; line-height: 1.2; }
  .contact__role { margin-bottom: 8px; }
  .contact__row { display: flex; align-items: center; gap: 8px; }
  .contact__row svg { width: 13px; height: 13px; flex: none; }
  .contact__gap { height: 6px; }
  .card--back .wordmark {
    position: absolute; left: 322px; top: 168px;
    color: var(--brand-blue);
  }
  .card--back .wordmark__name { font-size: 38px; }
  .card--back .wordmark__sub { font-size: 14px; letter-spacing: 0.6em; }
</style>
</head>
<body>
<main class="stage">

  <section class="card card--front" aria-label="Card front">
    <h1 class="wordmark">
      <span class="wordmark__name">Brambleford</span>
      <span class="wordmark__sub">Constructions</span>
    </h1>
    <p class="services">Roofing • Ceiling • Insulation • Gutter Guards<br>Electrical • Insurance etc</p>
  </section>

  <section class="card card--back" aria-label="Card back">
    <svg class="back-panel" viewBox="0 0 620 379" preserveAspectRatio="none" aria-hidden="true">
      <path d="M392 0 Q268 170 286 379 L620 379 L620 0 Z" fill="#ffffff"/>
      <path d="M410 -4 Q300 160 312 383" fill="none" stroke="#1358a2" stroke-width="4"/>
    </svg>

    <div class="contact">
      <p class="contact__name">Gareth Pennick</p>
      <p class="contact__role">Project Manager</p>
      <p>47C Corvell Street</p>
      <p>Malaga WA 6090</p>
      <p>PO Box: 3817 Malaga WA 6944</p>
      <div class="contact__gap"></div>
      <p class="contact__row">
        <svg viewBox="0 0 16 16" aria-hidden="true"><path d="M3 1h3l1.5 4-2 1.3a9 9 0 0 0 4.2 4.2L11 8.5l4 1.5v3a2 2 0 0 1-2 2A12 12 0 0 1 1 3a2 2 0 0 1 2-2z" fill="#fff"/></svg>
        (08) 9316 5172
      </p>
      <p class="contact__row">
        <svg viewBox="0 0 16 16" aria-hidden="true"><rect x="4" y="1" width="8" height="14" rx="1.5" fill="none" stroke="#fff" stroke-width="1.6"/><circle cx="8" cy="12.5" r="1" fill="#fff"/></svg>
        0427 351 804
      </p>
      <p class="contact__row">
        <svg viewBox="0 0 16 16" aria-hidden="true"><rect x="1" y="3" width="14" height="10" rx="1" fill="none" stroke="#fff" stroke-width="1.6"/><path d="M1.5 3.5 8 9l6.5-5.5" fill="none" stroke="#fff" stroke-width="1.4"/></svg>
        info@bramblefordhomes.com.au
      </p>
    </div>

    <p class="wordmark">
      <span class="wordmark__name">Brambleford</span>
      <span class="wordmark__sub">Constructions</span>
    </p>
  </section>

</main>
</body>
</html>
```